Upmarket Dessert Lounge needs a Business Card Design

We are an upmarket dessert lounge needing a business card to match our image.

We want something that is simple yet beautiful, feminine, classy, sophisticated and elegant. We want it to stand out and don't mind if it is bold.

The design should include our logo and colours of red or maroon with gold highlights. We don't mind if black is used.

Marlow & Quince

Target Market(s)

For those who like to indulge or treat themselves and give in to their temptations on good quality desserts.

Industry/Entity Type

Business

Requirements
Must have
• Must include our logo and our name

Marlow & Quince

M & Q

```html
<!DOCTYPE html>
<html lang="en">
<head>
<meta charset="utf-8">
<title>Marlow &amp; Quince — Business Card</title>
<link rel="stylesheet" href="https://fonts.googleapis.com/css2?family=Open+Sans:wght@400;600&display=swap">
<style>
  :root {
    --backdrop: #e9e6e2;
    --card: #ffffff;
    --maroon: #7e1d1c;
    --maroon-light: #a3282a;
    --peach: #f6c795;
    --ink: #2b2b2b;
  }
  * { margin: 0; padding: 0; box-sizing: border-box; }
  html, body { width: 1200px; height: 951px; overflow: hidden; }
  body {
    background: var(--backdrop);
    font-family: "Open Sans", Arial, sans-serif;
    position: relative;
  }
  .card {
    position: absolute;
    width: 700px;
    height: 400px;
    background: var(--card);
    border-radius: 22px;
    overflow: hidden;
    box-shadow: 0 10px 28px rgba(0,0,0,0.18);
  }
  .card--front { left: 90px; top: 70px; }
  .card--back { left: 410px; top: 480px; }

  .brand-name {
    position: absolute;
    color: var(--maroon);
    font-weight: 600;
    letter-spacing: 2px;
    text-transform: uppercase;
    white-space: nowrap;
  }
  .card--front .brand-name { left: 120px; top: 168px; font-size: 38px; }
  .card--back .brand-name { left: 60px; top: 64px; font-size: 30px; }

  .corner-ornament {
    position: absolute;
    right: 0; top: 0;
    width: 260px; height: 150px;
    background: radial-gradient(ellipse at 70% 35%, #f3c38f 0%, #f7d6b2 55%, rgba(255,255,255,0) 80%);
  }
  .front-web {
    position: absolute;
    left: 0; right: 0; bottom: 40px;
    text-align: center;
    font-size: 19px;
    letter-spacing: 2px;
    color: var(--ink);
  }

  .back-sweep { position: absolute; inset: 0; }
  .contact-list {
    position: absolute;
    left: 48px; top: 225px;
    list-style: none;
    font-size: 20px;
    line-height: 30px;
    color: var(--ink);
  }
  .contact-list li { display: flex; align-items: center; gap: 10px; }
  .contact-list svg { width: 16px; height: 16px; fill: var(--maroon); flex: none; }
  .contact-list .accent { color: var(--maroon); }
  .back-title {
    position: absolute;
    right: 46px; bottom: 52px;
    color: #ffffff;
    font-size: 28px;
    letter-spacing: 1px;
  }
</style>
</head>
<body>

  <section class="card card--front">
    <div class="corner-ornament" role="img" aria-label="Gold floral flourish in the corner"></div>
    <span class="brand-name">Marlow &amp; Quince</span>
    <p class="front-web">www.marlow&amp;quince.com</p>
  </section>

  <section class="card card--back">
    <svg class="back-sweep" viewBox="0 0 700 400" preserveAspectRatio="none" aria-hidden="true">
      <defs>
        <radialGradient id="maroonGlow" cx="0.7" cy="0.45" r="0.7">
          <stop offset="0" stop-color="#a3282a"/>
          <stop offset="1" stop-color="#7e1d1c"/>
        </radialGradient>
      </defs>
      <path d="M415 0 C370 140 320 280 235 400 L700 400 L700 0 Z" fill="#f6c795"/>
      <path d="M445 0 C405 140 360 280 280 400 L700 400 L700 0 Z" fill="#ffffff"/>
      <path d="M462 0 C425 140 385 280 310 400 L700 400 L700 0 Z" fill="url(#maroonGlow)"/>
    </svg>

    <span class="brand-name">Marlow &amp; Quince</span>

    <ul class="contact-list">
      <li><svg viewBox="0 0 16 16"><path d="M3 1h3l1.5 4-2 1.2a9 9 0 0 0 4.3 4.3L11 8.5 15 10v3a2 2 0 0 1-2 2A12 12 0 0 1 1 3a2 2 0 0 1 2-2z"/></svg>555-014-2200</li>
      <li><svg viewBox="0 0 16 16"><rect x="4" y="1" width="8" height="14" rx="1.5"/></svg>555-014-2201</li>
      <li><svg viewBox="0 0 16 16"><path d="M1 3h14v10H1z M1 3l7 6 7-6" stroke="#fff" stroke-width="1"/></svg>info@marlow&amp;quince.com</li>
      <li><svg viewBox="0 0 16 16"><circle cx="8" cy="8" r="7"/></svg>www.<span class="accent">marlow&amp;quince</span>.com</li>
    </ul>

    <p class="back-title">Marlow &amp; Quince</p>
  </section>

</body>
</html>
```